Zielgruppe
Wir sind Sydneys führender Brick and Stone Restorator.
Aufgabenstellung
Unsere neue webseite geht in ein paar tagen online und wir möchten gerne passenden zur neuen Webseite ein corporate Flyer, letztendlich soll es ein Print Version von unserer neuen Webseite sein. Sprich die wichtigsten Informationen der Webseite soll in dem Flyer enthalten sein. Letztendlich möchte ich designer keine großen einschränkungen geben, weil das ist euer job kreativ sein ;), aber der flyer sollte evtl. so aufgebaut sein das am Ende die leute entweder uns anrufen oder doch auf unsere neue Webseite gehen sprich evtl ein QR- code or what ever.
Unsere Domain ist ostravagrouting.com.au, aber damit ihr die neue Webseite schon sehen könnt müsst ihr auf ostravagrouting.com.au/ new, falls dieser Link nicht mehr funktionieren sollte, ist sie schon auf der richtigen domain hochgeladen.
Falls ihr irgendwelche Logos Bilder oder sonst was benötigt und diese nicht aus der Webseite entnehmen könnt, schickt einfach eine kurze Naricht, ich beantworte diese so schnell wie möglich ;)
der Flyer soll ein 6 pager sein!!
mit freundlichen Grüßen euer Ostrava Grouting Team

```html
<!DOCTYPE html>
<html lang="en">
<head>
<meta charset="utf-8">
<title>Ostrava Grouting – Brochure Spreads</title>
<link href="https://fonts.googleapis.com/css2?family=Outfit:wght@300;400;500;800&display=swap" rel="stylesheet">
<style>
  :root{
    --purple:#372c4f;
    --beige:#e9e0c5;
    --cream:#f3eedf;
    --white:#ffffff;
    --ink:#3a2f52;
  }
  html,body{margin:0;padding:0;width:1150px;height:1200px;overflow:hidden;background:var(--white);}
  .canvas{position:relative;width:1150px;height:1200px;overflow:hidden;background:var(--white);font-family:'Outfit',sans-serif;}
  .stage{position:absolute;left:0;top:0;width:1325px;height:1382px;transform:scale(0.8679);transform-origin:0 0;}
  .abs{position:absolute;}
  .photo{position:absolute;}
  .panel-purple{position:absolute;background:var(--purple);color:var(--white);}
  .band-beige{position:absolute;background:var(--beige);color:var(--ink);font-weight:300;font-size:15px;line-height:20px;padding-left:29px;box-sizing:border-box;white-space:nowrap;}
  .body-text{font-size:8.4px;line-height:10.9px;text-align:justify;margin:0;font-weight:400;}
  .services{display:flex;gap:38px;font-size:8.4px;line-height:11px;}
  .services ul{list-style:none;margin:0;padding:0;}
  .contact-row{position:absolute;display:flex;align-items:center;gap:10px;font-size:10.5px;line-height:14px;color:var(--white);}
  .contact-icon{width:29px;height:29px;border-radius:50%;background:var(--white);display:flex;align-items:center;justify-content:center;flex:none;}
  .brand{position:absolute;left:861px;top:58px;width:397px;height:188px;background:var(--white);display:flex;align-items:center;justify-content:center;}
  .brand-lockup{display:flex;align-items:flex-start;gap:10px;margin-top:-8px;}
  .brand-mark{width:14px;height:52px;background:var(--purple);display:block;flex:none;margin-top:2px;}
  .brand-text{display:flex;flex-direction:column;}
  .brand-name{font-weight:800;font-size:27px;color:var(--purple);letter-spacing:0.5px;line-height:28px;white-space:nowrap;}
  .brand-tag{font-weight:500;font-size:10.5px;color:var(--purple);letter-spacing:1px;line-height:14px;margin-top:8px;white-space:nowrap;}
  .hero-title{font-weight:800;font-size:20.5px;line-height:21px;text-align:center;color:var(--white);letter-spacing:0.3px;}
  .section-title{position:absolute;background:var(--white);color:var(--ink);font-weight:300;font-size:27px;line-height:28px;box-sizing:border-box;white-space:nowrap;}
  .list-title{font-weight:500;font-size:11.5px;text-decoration:underline;margin:0 0 8px;}
  .bullets{list-style:none;margin:0;padding:0;font-size:8.4px;line-height:10.9px;}
  .bullets li{padding-left:7px;text-indent:-7px;}
  .steps{margin:0;padding-left:12px;font-size:8.4px;line-height:10.4px;}
  .steps li{margin-bottom:5px;}
  .quote-note{position:absolute;color:var(--ink);font-weight:300;font-size:11.5px;line-height:16px;}
</style>
</head>
<body>
<div class="canvas">
 <div class="stage">

  <section class="spread spread-outside">
    <div class="photo" style="left:67px;top:58px;width:245px;height:190px;background:linear-gradient(180deg,#3e6b2c 0%,#3e6b2c 32%,#8a4a3a 40%,#5a3a44 70%,#7a4436 100%);" role="img" aria-label="Photo of a dark brick garden wall with a green hedge and iron railing behind"></div>
    <div class="photo" style="left:312px;top:58px;width:151px;height:190px;background:linear-gradient(135deg,#5a3f4c 0%,#7a4a3c 50%,#4a3440 100%);" role="img" aria-label="Close-up photo of a repointed brick pillar"></div>
    <div class="photo" style="left:463px;top:58px;width:397px;height:190px;background:linear-gradient(180deg,#b45a35 0%,#a8512f 100%);" role="img" aria-label="Photo of a red brick facade with a white sash window"></div>
    <div class="abs" style="left:67px;top:246px;width:1191px;height:8px;background:var(--cream);"></div>

    <div class="panel-purple" style="left:67px;top:254px;width:794px;height:399px;"></div>

    <div class="band-beige" style="left:67px;top:280px;width:364px;height:20px;">The Ostrava Grouting philosophy</div>
    <p class="body-text abs" style="left:96px;top:309px;width:336px;color:var(--white);">Bricks and mortar are the foundation of your home or building. Not only do you want a structurally strong and sound building, you also want the building’s integrity and historic character upheld and protected for years to come. This is exactly what the talented craftsmen at Ostrava Grouting believe and strive to achieve on each and every job they commit to. If you want the best brick pointing in Sydney, pick up the phone.</p>

    <div class="band-beige" style="left:67px;top:382px;width:364px;height:20px;">Why choose us?</div>
    <div class="abs" style="left:96px;top:411px;width:336px;color:var(--white);">
      <p class="body-text">Maintaining the bricks and mortar of your building in premium condition is about more than protecting the overall health of your building’s structure – it’s a complete investment in your building’s future. Be it domestic, commercial, strata complex or a heritage building, Ostrava Grouting cares for projects of all sizes. So if you’re seeking friendly, professional service from a team of highly skilled craftsmen with almost two decades experience in their field, Ostrava Grouting is for you.</p>
      <p class="body-text" style="margin-top:11px;">You don’t need any ordinary brick repointing firm. Your home is one of your most valuable assets, so you need a professional brick repointing team who treat it as such. Don’t let the value of your home or building slowly deteriorate along side crumbling brickwork or mortar. It’s easy to return your building to its former glory with Ostrava Grouting’s complete range of brick repointing services including:</p>
    </div>
    <div class="services abs" style="left:96px;top:579px;color:var(--white);">
      <ul><li>» Stone &amp; brick repointing</li><li>» Tuckpointing</li><li>» Brick restoration &amp; repair</li><li>» Brick staining</li></ul>
      <ul><li>» Wall tie replacement</li><li>» Arch-bar replacement</li><li>» Water repellent and brick sealing solutions</li><li>» Heritage projects</li></ul>
    </div>

    <p class="abs" style="left:547px;top:296px;width:230px;margin:0;font-size:10.5px;line-height:14px;color:var(--white);">Ostrava Grouting are located in Sydney’s Eastern Suburbs and cater to all areas.</p>
    <div class="contact-row" style="left:547px;top:349px;">
      <span class="contact-icon"><svg width="16" height="16" viewBox="0 0 16 16"><path d="M8 2 L1.5 8 H3.5 V14 H6.5 V10 H9.5 V14 H12.5 V8 H14.5 Z" fill="var(--purple)"/></svg></span>
      <span>PO Box 4127, Coogee Vale,<br>NSW 2099</span>
    </div>
    <div class="contact-row" style="left:547px;top:409px;">
      <span class="contact-icon"><svg width="15" height="15" viewBox="0 0 16 16"><path d="M4 1.5 L6.5 4.5 L5 6.5 C5.8 8.4 7.6 10.2 9.5 11 L11.5 9.5 L14.5 12 L12.5 14.5 C7 14 2 9 1.5 3.5 Z" fill="var(--purple)"/></svg></span>
      <span>Office phone: 0400 555 017</span>
    </div>
    <div class="contact-row" style="left:547px;top:461px;">
      <span class="contact-icon"><svg width="16" height="16" viewBox="0 0 16 16" fill="none" stroke="var(--purple)" stroke-width="1.3"><circle cx="8" cy="8" r="6.2"/><ellipse cx="8" cy="8" rx="2.6" ry="6.2"/><path d="M1.8 8 H14.2 M3 4.8 H13 M3 11.2 H13"/></svg></span>
      <span>www.ostravagrouting.com.au</span>
    </div>
    <div class="photo" style="left:548px;top:506px;width:211px;height:85px;background:linear-gradient(120deg,#eeece6 0%,#e4e2db 65%,#b9d4e6 78%,#a9cbe3 100%);border:2px solid #c9c4d6;box-sizing:border-box;" role="img" aria-label="Street map showing the office location in Sydney's Eastern Suburbs"></div>
    <p class="abs" style="left:547px;top:609px;margin:0;font-size:10.5px;color:var(--white);">Licence no: 418756K</p>

    <div class="brand">
      <div class="brand-lockup">
        <span class="brand-mark"></span>
        <div class="brand-text">
          <span class="brand-name">OSTRAVA</span>
          <span class="brand-name">GROUTING</span>
          <span class="brand-tag">BRICK AND STONE RESTORATION</span>
        </div>
      </div>
    </div>
    <div class="photo" style="left:861px;top:254px;width:397px;height:399px;background:linear-gradient(180deg,#f2f2ef 0%,#5d5a58 18%,#3f3b3d 45%,#7b6a52 70%,#4a4240 100%);" role="img" aria-label="Photo of a gothic stone church facade with a large tracery window"></div>
    <div class="abs" style="left:861px;top:505px;width:397px;height:83px;background:rgba(55,44,79,0.93);display:flex;align-items:center;justify-content:center;">
      <div class="hero-title">SYDNEY’S BRICK AND<br>STONE RESTORATION AND<br>BRICK REPOINTING EXPERTS</div>
    </div>
  </section>

  <section class="spread spread-inside">
    <div class="photo" style="left:67px;top:707px;width:383px;height:221px;background:linear-gradient(180deg,#f1efe9 0%,#b06a52 35%,#9c5440 70%,#cfc8bc 100%);" role="img" aria-label="Photo of a heritage brick building under scaffolding"></div>
    <div class="section-title" style="left:67px;top:857px;width:236px;height:72px;padding:12px 0 0 29px;">Heritage Brick<br>Restoration</div>
    <div class="panel-purple" style="left:67px;top:929px;width:236px;height:188px;padding:18px 0 0 30px;box-sizing:border-box;">
      <p class="list-title">HERITAGE WORKS INCLUDE:</p>
      <ul class="bullets" style="width:190px;">
        <li>» Stone and brick façade restoration</li>
        <li>» Structural repair</li>
        <li>» Heritage Brick Restoration</li>
        <li>» Repointing</li>
        <li>» Tuckpointing (white or black line)</li>
        <li>» Damp issues (Ostrava Grouting uses waterproofing products from heritage experts – Kelbrook Remedial)</li>
        <li>» Specially formulated heritage mortar (Ostrava Grouting uses the highest quality mortar products developed by heritage brick restoration experts – Marlow Mortars)</li>
      </ul>
    </div>
    <p class="quote-note" style="left:326px;top:986px;width:122px;margin:0;">The Ostrava Grouting team have accomplished restoration works for heritage buildings throughout NSW.</p>
    <div class="photo" style="left:67px;top:1123px;width:377px;height:178px;background:linear-gradient(90deg,#a3503c 0%,#c9c2b4 30%,#9a4a37 55%,#d2cbbd 80%,#a4533f 100%);" role="img" aria-label="Photo of a heritage brick entrance with memorial plaques"></div>

    <div class="photo" style="left:479px;top:707px;width:364px;height:283px;background:linear-gradient(180deg,#6e9fd1 0%,#8f5a4b 22%,#7a4b44 60%,#8e5647 100%);" role="img" aria-label="Photo of a multi-storey residential red brick apartment block"></div>
    <div class="section-title" style="left:479px;top:990px;width:315px;height:77px;padding:10px 0 0 24px;">Residental bricks and<br>stone restoration</div>
    <div class="panel-purple" style="left:479px;top:1067px;width:335px;height:221px;padding:14px 20px 0 22px;box-sizing:border-box;">
      <p class="list-title" style="margin-bottom:4px;">REPOINTING</p>
      <p class="body-text">What is repointing? Repointing is an intricate process requiring a high level of proficiency and experience to ensure the integrity of your building is upheld.</p>
      <p class="body-text" style="margin:10px 0 5px;">The repointing process:</p>
      <ol class="steps">
        <li>Decayed mortar is carefully raked out of the brick or stone joints and the joints are then washed to remove any dust and debris</li>
        <li>Depending on your building, Ostrava Grouting will inspect the original joint and mortar type – creating a new mortar closely matching the original colour and texture</li>
        <li>Mortar is injected into the joint, with careful consideration taken to ensure the original joint profile is correct</li>
        <li>Once the mortar is dry, your brickwork is thoroughly cleaned with a high-pressure water brick cleaning system</li>
      </ol>
    </div>

    <div class="photo" style="left:1002px;top:707px;width:256px;height:333px;background:linear-gradient(180deg,#efece6 0%,#a04a3a 30%,#8e3f33 70%,#b45a45 100%);" role="img" aria-label="Photo of a restored red brick house with bay windows"></div>
    <div class="section-title" style="left:883px;top:742px;width:234px;height:70px;padding:9px 0 0 14px;">Decorative Brick<br>&amp; Stone finishes</div>
    <div class="panel-purple" style="left:883px;top:812px;width:274px;height:225px;padding:11px 10px 0 15px;box-sizing:border-box;">
      <p class="body-text">If you’re an owner of a brick home or building, you could be faced with brickwork problems that result in disrepair, crumbling or collapse. When reversing the damage to your stone or brickwork you’ll want to ensure your building is restored safely, while maintaining its original character and integrity. Your home or heritage building may be experiencing fretting, bowed or loose brickwork. Once this process starts it can potentially lead to cracks on the outside of the brickwork, ultimately requiring extensive mortar and brick repair.</p>
      <p class="body-text" style="margin-top:11px;">If your home or heritage building is located in Sydney, it’s more than likely that your building is experiencing a high occurrence of salt intolerance. Salt crystals can stick to the surface of your brickwork, gradually eating away at the structure and causing deterioration. Restore your building and prevent further damage with Ostrava Grouting’s water repellent products and brick sealing solutions, which can be applied to prevent further infiltration of water.</p>
    </div>
    <div class="photo" style="left:883px;top:1047px;width:375px;height:254px;background:linear-gradient(180deg,#d8d4cc 0%,#9a3f30 25%,#7e3328 60%,#8fa06a 85%,#e9e6e0 100%);" role="img" aria-label="Photo of a red brick house porch with white columns and tiled steps"></div>
  </section>

 </div>
</div>
</body>
</html>
```